Inspirational Quotes Poster Set

Brookloft is a stylish coworking space, which has a design-oriented vintage look from the 60's with an industrial touch (www.brookloft-example.com) Brookloft Quote Poster Set of 16 posters. The poster should be typo oriented and rather simple. Reflecting a bit the clean billboard design from the sixties. Minimal / simple graphical elements

Target Market(s)

Startups and Entrepreneurs

Industry/Entity Type

Startup

Font styles to use
Sans Serif

Colors

Designer to choose colors to be used in the design.

Requirements
Must have
• Posters need to be on and very stylish

```html
<!DOCTYPE html>
<html lang="en">
<head>
<meta charset="utf-8">
<title>Brookloft Quote Poster Set – Always Challenge the Old Ways</title>
<link rel="stylesheet" href="https://fonts.googleapis.com/css2?family=Bebas+Neue&family=Kaushan+Script&family=Carlito:wght@700&display=swap">
<style>
  :root {
    --paper: #ffe8c1;
    --ink: #000000;
    --accent: #ef5322;
    --accent-soft: #f59a76;
  }
  html, body {
    margin: 0;
    padding: 0;
    overflow: hidden;
    background: var(--paper);
  }
  .poster {
    position: relative;
    width: 738px;
    height: 1200px;
    background: var(--paper);
    overflow: hidden;
    color: var(--ink);
  }
  .quote-lead {
    position: absolute;
    left: 0;
    width: 738px;
    top: 170px;
    margin: 0;
    text-align: center;
    font-family: "Kaushan Script", cursive;
    font-weight: 400;
    font-size: 132px;
    line-height: 1;
  }
  .jump-figure {
    position: absolute;
    left: 336px;
    top: 326px;
    width: 80px;
    height: 102px;
    background: var(--accent-soft);
    border-radius: 6px;
  }
  .gap-ledges {
    position: absolute;
    left: 0;
    top: 0;
  }
  .gap-ledges .ledge { fill: var(--accent); }
  .quote-main {
    position: absolute;
    left: 0;
    width: 738px;
    margin: 0;
    text-align: center;
    font-family: "Bebas Neue", sans-serif;
    font-weight: 400;
    line-height: 1;
  }
  .quote-main--large {
    top: 520px;
    font-size: 156px;
    letter-spacing: 1px;
  }
  .quote-main--small {
    top: 672px;
    font-size: 101px;
    letter-spacing: 1px;
  }
  .attribution {
    position: absolute;
    left: 0;
    width: 738px;
    top: 1006px;
    margin: 0;
    text-align: center;
    font-family: "Carlito", "Calibri", sans-serif;
    font-weight: 700;
    font-size: 40px;
    line-height: 51px;
  }
  .attribution span { display: block; }
</style>
</head>
<body>
  <main class="poster">
    <p class="quote-lead">Always</p>

    <div class="jump-figure" role="img" aria-label="Orange stick figure leaping across a gap"></div>

    <svg class="gap-ledges" width="738" height="1200" viewBox="0 0 738 1200" aria-hidden="true">
      <polygon class="ledge" points="269,442 322,442 300,503 269,503"/>
      <polygon class="ledge" points="426,442 478,442 478,503 447,503"/>
    </svg>

    <h1 class="quote-main quote-main--large">Challenge</h1>
    <h2 class="quote-main quote-main--small">The Old Ways</h2>

    <p class="attribution">
      <span>Harold Sterling</span>
      <span>CEO Beanhouse</span>
    </p>
  </main>
</body>
</html>
```